Business Card Design

Business Card for professional consulting firm working with large financial institutions.

Target Market(s)

Executive buyers

Industry/Entity Type

Banking

Contact Information for Business Card

Mild creativity wanted. Not boring, but do elaborate artwork.

Font styles to use
Serif
Sans Serif

Colors

Designer to choose colors to be used in the design.

Requirements
Must have
• Standard business card features - company name, individual name, telephone, website, email, locations.
Nice to have
• Two colors
Should not have
• too many colors, fancy printing, cartoons.

```html
<!DOCTYPE html>
<html lang="en">
<head>
<meta charset="utf-8">
<title>Harlow Advisory Business Card</title>
<link rel="stylesheet" href="https://fonts.googleapis.com/css2?family=Alegreya:wght@400&family=Roboto:wght@400&family=Roboto+Condensed:wght@700&display=swap">
<style>
  :root {
    --backdrop: #d9d4cd;
    --card-white: #f4f4f4;
    --ink: #111111;
    --ink-soft: #3a3a3a;
    --muted: #9a9a9a;
    --rule: #8c8c8c;
    --band-grey: #c4c4c4;
    --band-black: #050505;
    --paper-white: #ffffff;
  }
  * { margin: 0; padding: 0; box-sizing: border-box; }
  html, body {
    width: 1200px; height: 960px; overflow: hidden;
    background: var(--backdrop);
  }
  .stage { position: relative; width: 1200px; height: 960px; }

  .card {
    position: absolute;
    width: 598px; height: 342px;
    box-shadow: 0 3px 8px rgba(0,0,0,0.35);
    overflow: hidden;
  }
  .card--front { left: 322px; top: 108px; background: var(--card-white); }
  .card--back { left: 321px; top: 493px; background: var(--band-black); }

  .brand-name {
    position: absolute;
    font-family: "Roboto", Arial, sans-serif;
    font-weight: 400;
    color: var(--ink);
    white-space: nowrap;
  }
  .card--front .brand-name { right: 50px; top: 60px; font-size: 26px; }
  .card--back .brand-name {
    left: 0; right: 0; top: 136px; text-align: center;
    font-size: 48px; color: var(--paper-white);
  }

  .person-name {
    position: absolute; left: 33px; top: 186px;
    font-family: "Roboto Condensed", Arial, sans-serif;
    font-weight: 700; font-size: 23px; color: var(--ink);
  }
  .person-title {
    position: absolute; left: 33px; top: 213px;
    font-family: "Roboto", Arial, sans-serif;
    font-size: 14px; color: var(--muted); letter-spacing: 0.3px;
  }
  .divider {
    position: absolute; left: 33px; right: 33px; top: 240px;
    height: 1px; background: var(--rule);
  }
  .contact, .address {
    position: absolute; top: 258px;
    font-family: "Roboto", Arial, sans-serif;
    font-size: 14px; line-height: 19px; color: var(--ink-soft);
    list-style: none; font-style: normal;
  }
  .contact { left: 33px; }
  .contact li { display: flex; align-items: center; gap: 8px; }
  .contact svg { width: 13px; height: 13px; fill: var(--ink); }
  .address { right: 30px; text-align: right; }

  .footer-band { position: absolute; left: 0; bottom: 0; width: 598px; height: 34px; }
  .website {
    position: absolute; right: 15px; bottom: 6px;
    font-family: "Alegreya", Georgia, serif;
    font-size: 15px; letter-spacing: 1.6px; color: var(--paper-white);
    white-space: nowrap;
  }
</style>
</head>
<body>
<main class="stage">
  <section class="card card--front" aria-label="Card front">
    <div class="brand-name">Harlow Advisory</div>

    <h1 class="person-name">MARK ELLISON</h1>
    <p class="person-title">CEO/FOUNDER</p>
    <div class="divider"></div>

    <ul class="contact">
      <li>
        <svg viewBox="0 0 24 24" aria-hidden="true"><path d="M6.6 10.8a15.1 15.1 0 0 0 6.6 6.6l2.2-2.2a1 1 0 0 1 1-.25 11.4 11.4 0 0 0 3.6.57 1 1 0 0 1 1 1V20a1 1 0 0 1-1 1A17 17 0 0 1 3 4a1 1 0 0 1 1-1h3.5a1 1 0 0 1 1 1c0 1.25.2 2.45.57 3.57a1 1 0 0 1-.25 1z"/></svg>
        555 210 4817
      </li>
      <li>
        <svg viewBox="0 0 24 24" aria-hidden="true"><path d="M2 5h20v14H2z" fill="var(--ink)"/><path d="M3 6l9 7 9-7" fill="none" stroke="var(--card-white)" stroke-width="1.6"/></svg>
        info@harlowadvisory.com
      </li>
    </ul>

    <address class="address">
      2318 Linden Court<br>
      Fairbanks, Alaska 99701
    </address>

    <svg class="footer-band" viewBox="0 0 598 34" aria-hidden="true">
      <polygon points="0,8 345,8 332,24 0,24" fill="var(--band-grey)"/>
      <polygon points="350,0 598,0 598,34 0,34 0,24 330,24" fill="var(--band-black)"/>
    </svg>
    <div class="website">www.harlowadvisory.com</div>
  </section>

  <section class="card card--back" aria-label="Card back">
    <div class="brand-name">Harlow Advisory</div>
  </section>
</main>
</body>
</html>
```